Sophisticated, clean website reflecting my feminine, playful side to sell my abstract art,

I need a website no more than 3 pages to showcase my paintings, a little about me and some contact info. I do abstracts so looking for something a little edgy, yet feminine and current.
Updates

Hi there, These are some artists websites that I Iike: Marnelvoss.com (I like how airy it is) peterwallombry.com garethpolvens.com (I like how it scrolls) I'll need a place for a photo ( a headshot-i do not have it yet so I'll need to be able to upload that later) as well as an area for my bio. Also, it's important that I will be able to upload any new photos and descriptions easily so it should be user friendly. Lastly, I like in a sunny place so would like to have this seem upbeat and playful as that is how i like to paint. thanks-I'm trying to upload my photos now -

Target Market(s)

ppl ages 35-70 who want large scale art for their homes

Industry/Entity Type

art

Coding

Coded - Design and coding required

Number of Pages Required

3 page

Colors

Designer to choose colors to be used in the design.

Requirements
Must have
• photos of my art, a place for my bio, be easy to reach me. tasteful-nothing too "in your face" -my clients are pretty high end and organized. They like clean lines
Nice to have
• sophisticated background, muted tones in the back-similar clean font throughout-no cursive
Should not have
• too many dark areas. Too many blocks of color. Too serious.

```html
<!DOCTYPE html>
<html lang="en">
<head>
<meta charset="utf-8">
<title>Lena Marwick Art</title>
<link rel="stylesheet" href="https://fonts.googleapis.com/css2?family=Mulish:wght@400;600;700;800;900&display=swap">
<style>
  :root {
    --blue: #1b6ec2;
    --blue-dark: #135aa3;
    --ink: #1e1e1e;
    --text: #333333;
    --muted: #8a8a8a;
    --line: #cfcfcf;
    --white: #ffffff;
    --footer: #1b1b1b;
    --panel: rgba(255,255,255,0.9);
  }
  * { box-sizing: border-box; margin: 0; padding: 0; }
  html, body { width: 1200px; height: 2328px; overflow: hidden; }
  body { font-family: "Mulish", Arial, sans-serif; color: var(--text); background: var(--white); position: relative; }

  .site-header { position: absolute; top: 0; left: 0; width: 1200px; height: 88px; display: flex; align-items: center; justify-content: space-between; padding: 0 128px; }
  .brand { font-size: 24px; font-weight: 800; color: var(--ink); }
  .main-nav { display: flex; gap: 44px; font-size: 13px; font-weight: 700; letter-spacing: .5px; color: var(--ink); }

  .hero { position: absolute; top: 88px; left: 0; width: 1200px; height: 577px; }
  .hero-art { position: absolute; left: 0; top: 0; width: 776px; height: 577px;
    background: radial-gradient(circle at 30% 40%, #e9c9cc 0, #c98f9a 22%, #8a6f86 45%, #d9c6c4 70%, #b8a3b3 100%); }
  .hero-caption { position: absolute; left: 200px; top: 222px; color: var(--white); }
  .hero-caption h1 { font-size: 38px; font-weight: 900; letter-spacing: .5px; text-shadow: 0 2px 8px rgba(0,0,0,.35); }
  .hero-caption p { font-size: 17px; font-weight: 600; margin-top: 4px; text-shadow: 0 1px 6px rgba(0,0,0,.4); }
  .slider-dots { position: absolute; left: 336px; top: 540px; display: flex; gap: 8px; }
  .slider-dots span { width: 11px; height: 11px; border-radius: 50%; background: rgba(255,255,255,.6); }
  .slider-dots span:first-child { background: var(--white); }

  .about-panel { position: absolute; left: 776px; top: 0; width: 424px; height: 577px; background: var(--blue); padding: 32px 36px; color: var(--white); }
  .headshot { width: 160px; height: 172px; background: linear-gradient(160deg, #d8dde3, #9aa6b3); border: 3px solid rgba(255,255,255,.7); }
  .about-panel h2 { font-size: 20px; font-weight: 800; margin-top: 44px; }
  .about-panel p { font-size: 15px; line-height: 1.45; margin-top: 10px; max-width: 320px; }
  .btn-light { display: inline-block; margin-top: 30px; background: var(--white); color: var(--blue); font-size: 13px; font-weight: 800; padding: 9px 20px; letter-spacing: .5px; }

  .gallery { position: absolute; top: 665px; left: 0; width: 1200px; height: 955px; }
  .section-title { position: absolute; left: 50%; transform: translateX(-50%); border: 2px solid var(--ink); padding: 8px 16px; font-size: 20px; font-weight: 900; color: var(--ink); background: var(--white); letter-spacing: .5px; }
  .section-title::after { content: ""; position: absolute; inset: 4px; border: 1px solid var(--ink); pointer-events: none; }
  .gallery .section-title { top: 150px; }
  .painting-grid { position: absolute; left: 128px; top: 213px; width: 944px; display: grid; grid-template-columns: repeat(3, 284px); grid-auto-rows: 300px; column-gap: 46px; row-gap: 26px; }
  .painting-card { border: 2px solid var(--line); padding: 10px; position: relative; background: var(--white); box-shadow: 0 2px 6px rgba(0,0,0,.08); }
  .painting-image { width: 100%; height: 100%; }
  .painting-label { position: absolute; left: 50%; bottom: 16px; transform: translateX(-50%); background: rgba(30,30,30,.82); color: var(--white); font-size: 12px; font-weight: 800; padding: 6px 16px; letter-spacing: .5px; white-space: nowrap; }
  .p1 { background: linear-gradient(150deg, #e7e4ef, #6b6a9c 45%, #c6b3d0); }
  .p2 { background: linear-gradient(150deg, #f1e2d6, #9c3b22 45%, #e1b893); }
  .p3 { background: linear-gradient(150deg, #e8e1ea, #b7839a 45%, #efe7ec); }
  .p4 { background: linear-gradient(150deg, #f2efe9, #4c5f9a 45%, #d9c65a); }
  .p5 { background: linear-gradient(180deg, #f4f1ee 20%, #3f7fb0 60%, #e9e9ef); }
  .p6 { background: linear-gradient(150deg, #6b3440, #c58a90 45%, #3c2f3a); }
  .btn-blue { position: absolute; left: 50%; top: 888px; transform: translateX(-50%); background: var(--blue); color: var(--white); font-size: 13px; font-weight: 800; padding: 11px 22px; letter-spacing: .5px; white-space: nowrap; }

  .contact { position: absolute; top: 1620px; left: 0; width: 1200px; height: 540px; }
  .contact-art { position: absolute; inset: 0; background: linear-gradient(90deg, #3c5a7a 0%, #8fb3b5 25%, #1f7b82 50%, #2a5f8f 75%, #1d3557 100%); }
  .contact .section-title { top: 56px; }
  .section-title .accent { color: var(--blue); }
  .contact-panel { position: absolute; left: 200px; top: 124px; width: 800px; height: 360px; background: var(--panel); padding: 30px 36px; display: flex; gap: 40px; }
  .contact-info { width: 280px; }
  .contact-panel h3 { font-size: 17px; font-weight: 900; color: var(--ink); margin-bottom: 16px; }
  .info-item { display: flex; gap: 12px; align-items: flex-start; margin-bottom: 18px; font-size: 13px; line-height: 1.4; }
  .info-icon { flex: none; width: 28px; height: 28px; border-radius: 50%; background: var(--blue); display: flex; align-items: center; justify-content: center; }
  .message-form { flex: 1; }
  .form-row { display: flex; gap: 14px; margin-bottom: 14px; }
  .field { flex: 1; height: 34px; border: 1px solid var(--line); background: var(--white); font-size: 10px; color: var(--muted); padding: 10px; letter-spacing: .5px; }
  .field.message { height: 104px; }
  .btn-submit { display: inline-block; margin-top: 12px; background: var(--blue); color: var(--white); font-size: 12px; font-weight: 800; padding: 9px 16px; }

  .site-footer { position: absolute; top: 2160px; left: 0; width: 1200px; height: 168px; background: var(--footer); color: var(--white); padding: 0 128px; }
  .footer-top { display: flex; justify-content: space-between; align-items: center; height: 104px; border-bottom: 1px solid #444; }
  .footer-top .brand { color: var(--white); }
  .footer-top .main-nav { color: var(--white); }
  .footer-bottom { display: flex; justify-content: space-between; align-items: center; height: 60px; font-size: 11px; }
  .follow { display: flex; align-items: center; gap: 10px; font-weight: 700; letter-spacing: .5px; }
  .social-dot { width: 22px; height: 22px; border-radius: 50%; background: #6d6d6d; }
</style>
</head>
<body>
  <header class="site-header">
    <div class="brand">Lena Marwick Art</div>
    <nav class="main-nav"><span>PAINTINGS</span><span>ABOUT ME</span><span>CONTACT ME</span></nav>
  </header>

  <section class="hero">
    <div class="hero-art" role="img" aria-label="Abstract floral painting in rose, mauve and cream swirls"></div>
    <div class="hero-caption">
      <h1>ABSTRACT PAINTINGS</h1>
      <p>Lorem Ipsum is simply dummy text of the printing</p>
    </div>
    <div class="slider-dots"><span></span><span></span><span></span><span></span></div>
    <aside class="about-panel">
      <div class="headshot" role="img" aria-label="Portrait photo of the artist"></div>
      <h2>ABOUT ME</h2>
      <p>There are many variations of passages of Lorem Ipsum available, but the majority have suffered alteration in some form, by injected humour, or randomised words which don't look even slightly believable. If you are going to use a passage of Lorem Ipsum, you need to be sure there isn't anything embarrassing hidden in the middle of text.</p>
      <span class="btn-light">READ MORE</span>
    </aside>
  </section>

  <section class="gallery">
    <h2 class="section-title">GALLERY</h2>
    <div class="painting-grid">
      <div class="painting-card"><div class="painting-image p1" role="img" aria-label="Abstract painting in violet and white"></div><span class="painting-label">PAINTING 1</span></div>
      <div class="painting-card"><div class="painting-image p2" role="img" aria-label="Abstract painting in rust red and cream swirls"></div><span class="painting-label">PAINTING 2</span></div>
      <div class="painting-card"><div class="painting-image p3" role="img" aria-label="Abstract painting in soft pink and mauve"></div><span class="painting-label">PAINTING 3</span></div>
      <div class="painting-card"><div class="painting-image p4" role="img" aria-label="Abstract painting with blue and gold circles"></div><span class="painting-label">PAINTING 4</span></div>
      <div class="painting-card"><div class="painting-image p5" role="img" aria-label="Abstract painting with blue drips on white"></div><span class="painting-label">PAINTING 5</span></div>
      <div class="painting-card"><div class="painting-image p6" role="img" aria-label="Abstract painting in deep burgundy and pink"></div><span class="painting-label">PAINTING 6</span></div>
    </div>
    <span class="btn-blue">VIEW ALL PAINTINGS</span>
  </section>

  <section class="contact">
    <div class="contact-art" role="img" aria-label="Abstract painting with teal and navy vertical brushstrokes"></div>
    <h2 class="section-title">CONTACT <span class="accent">ME</span></h2>
    <div class="contact-panel">
      <div class="contact-info">
        <h3>CONTACT US</h3>
        <div class="info-item">
          <span class="info-icon"><svg width="14" height="14" viewBox="0 0 24 24"><path d="M12 2a7 7 0 0 0-7 7c0 5 7 13 7 13s7-8 7-13a7 7 0 0 0-7-7zm0 9.5A2.5 2.5 0 1 1 12 6a2.5 2.5 0 0 1 0 5.5z" fill="#fff"/></svg></span>
          <span>418 Harbor Palm Ave Suite 12<br>Sarasota, FL 34236</span>
        </div>
        <div class="info-item">
          <span class="info-icon"><svg width="14" height="14" viewBox="0 0 24 24"><path d="M6.6 10.8a15 15 0 0 0 6.6 6.6l2.2-2.2a1 1 0 0 1 1-.25 11.4 11.4 0 0 0 3.6.57 1 1 0 0 1 1 1V20a1 1 0 0 1-1 1A17 17 0 0 1 3 4a1 1 0 0 1 1-1h3.5a1 1 0 0 1 1 1c0 1.25.2 2.45.57 3.57a1 1 0 0 1-.25 1z" fill="#fff"/></svg></span>
          <span>Call Me<br>1-555-204-7781</span>
        </div>
        <div class="info-item">
          <span class="info-icon"><svg width="12" height="12" viewBox="0 0 24 24"><rect x="3" y="3" width="18" height="18" rx="5" fill="none" stroke="#fff" stroke-width="2.5"/></svg></span>
          <span>My Instagram<br>@lenamarwickart</span>
        </div>
      </div>
      <form class="message-form">
        <h3>SEND MESSAGE</h3>
        <div class="form-row"><div class="field">FIRST NAME</div><div class="field">LAST NAME</div></div>
        <div class="form-row"><div class="field">EMAIL ID</div><div class="field">PHONE</div></div>
        <div class="field message">MESSAGE</div>
        <span class="btn-submit">SUBMIT</span>
      </form>
    </div>
  </section>

  <footer class="site-footer">
    <div class="footer-top">
      <div class="brand">Lena Marwick Art</div>
      <nav class="main-nav"><span>PAINTINGS</span><span>ABOUT ME</span><span>CONTACT ME</span></nav>
    </div>
    <div class="footer-bottom">
      <div class="follow">FOLLOW US <span class="social-dot"></span><span class="social-dot"></span><span class="social-dot"></span></div>
      <div>Copyright © 2022 All Rights Reserved</div>
    </div>
  </footer>
</body>
</html>
```